Moravel Aesthetic Doctor

I require an elegant, luxurious looking business card for my aesthetic business. I am a doctor and that will set me aside from competitors. I am planning to provide home and spa based treatments to clients with high expectations. I have attached my logo.

```html
<!DOCTYPE html>
<html lang="en">
<head>
<meta charset="utf-8">
<title>Moravel Aesthetic Doctor – Business Card</title>
<link href="https://fonts.googleapis.com/css2?family=Roboto:wght@300;400;500&display=swap" rel="stylesheet">
<style>
  :root {
    --page-bg: #e6e6e6;
    --card-white: #ffffff;
    --card-grey: #a8aaad;
    --brand-blue: #5dbde9;
    --text-grey: #8d8f92;
    --rule-grey: #b3b5b8;
    --band-grey: #a8aaad;
    --white: #ffffff;
  }
  * { margin: 0; padding: 0; box-sizing: border-box; }
  html, body {
    width: 1125px; height: 1200px; overflow: hidden;
    background: var(--page-bg);
    font-family: "Roboto", Arial, sans-serif;
  }
  .card {
    position: absolute; left: 150px; width: 825px; height: 472px;
    border-radius: 24px; overflow: hidden;
    box-shadow: 0 3px 8px rgba(0,0,0,0.18);
  }
  .card--front { top: 98px; background: var(--card-white); }
  .card--back { top: 630px; background: var(--card-grey); }

  .wordmark { position: absolute; display: flex; align-items: center; gap: 16px; font-weight: 300; }
  .wordmark__dot { border-radius: 50%; flex: none; }
  .wordmark__name { line-height: 1; }
  .wordmark__name span { display: block; }

  .card--front .wordmark { right: 52px; top: 58px; color: var(--text-grey); }
  .card--front .wordmark__dot { width: 70px; height: 70px; border: 3px solid var(--rule-grey); }
  .card--front .wordmark__primary { font-size: 58px; letter-spacing: 1px; text-align: right; }
  .card--front .wordmark__secondary { font-size: 25px; letter-spacing: 2px; text-align: right; margin-top: 6px; }

  .card__halo {
    position: absolute; border-radius: 50%;
    border: 10px solid rgba(168,170,173,0.07);
  }
  .card--front .card__halo { left: 130px; top: 110px; width: 330px; height: 330px; }
  .card--back .card__halo { left: 310px; top: 20px; width: 470px; height: 470px; border-color: rgba(255,255,255,0.08); border-width: 16px; }

  .identity { position: absolute; left: 52px; top: 236px; width: 721px; }
  .identity__name { color: var(--brand-blue); font-size: 29px; font-weight: 500; }
  .identity__post { font-size: 19px; font-weight: 500; }
  .identity__qualification { color: var(--text-grey); font-size: 21px; font-weight: 300; margin-top: 6px; }
  .identity__rule { height: 2px; background: var(--rule-grey); margin-top: 8px; }

  .contacts { position: absolute; left: 52px; top: 317px; list-style: none; }
  .contacts li { display: flex; align-items: center; height: 33px; color: var(--text-grey); font-size: 21px; font-weight: 300; }
  .contacts svg { width: 18px; height: 18px; margin-right: 14px; fill: none; stroke: var(--brand-blue); stroke-width: 1.8; }
  .contacts .accent { color: var(--brand-blue); }

  .social { position: absolute; right: 52px; top: 393px; display: flex; gap: 20px; }
  .social__dot { width: 26px; height: 26px; border-radius: 50%; background: var(--brand-blue); }

  .card__band { position: absolute; left: 0; bottom: 0; width: 825px; height: 20px; }

  .card--back .wordmark { left: 160px; top: 128px; color: var(--white); }
  .card--back .wordmark__dot { width: 130px; height: 130px; border: 4px solid var(--white); }
  .card--back .wordmark__primary { font-size: 74px; letter-spacing: 1px; }
  .card--back .wordmark__secondary { font-size: 32px; letter-spacing: 2px; margin-top: 8px; }

  .services { position: absolute; left: 0; right: 0; top: 328px; text-align: center; color: var(--white); font-size: 22px; font-weight: 300; line-height: 33px; }
  .services .sep { font-size: 14px; vertical-align: middle; margin: 0 5px; }
</style>
</head>
<body>
  <section class="card card--front">
    <div class="card__halo"></div>
    <div class="wordmark">
      <div class="wordmark__dot"></div>
      <div class="wordmark__name">
        <span class="wordmark__primary">MORAVEL</span>
        <span class="wordmark__secondary">AESTHETIC DOCTOR</span>
      </div>
    </div>

    <div class="identity">
      <p class="identity__name">Dr Elise Varkon, <span class="identity__post">MRCPCH MD</span></p>
      <p class="identity__qualification">Australasian Diploma of Aesthetic Medicine</p>
      <div class="identity__rule"></div>
    </div>

    <ul class="contacts">
      <li><svg viewBox="0 0 24 24"><path d="M5 3h4l2 5-3 2a12 12 0 0 0 6 6l2-3 5 2v4a2 2 0 0 1-2 2A18 18 0 0 1 3 5a2 2 0 0 1 2-2z"/></svg>0800 457 309</li>
      <li><svg viewBox="0 0 24 24"><rect x="3" y="5" width="18" height="14" rx="1"/><path d="M3 6l9 7 9-7"/></svg>elise@moravel.co.nz</li>
      <li><svg viewBox="0 0 24 24"><circle cx="12" cy="12" r="9"/><path d="M3 12h18M12 3c3 3 3 15 0 18M12 3c-3 3-3 15 0 18"/></svg>www.<span class="accent">moravel</span>.co.nz</li>
    </ul>

    <div class="social">
      <div class="social__dot"></div>
      <div class="social__dot"></div>
    </div>

    <svg class="card__band" viewBox="0 0 825 20" preserveAspectRatio="none">
      <polygon points="0,0 605,0 595,20 0,20" fill="var(--band-grey)"/>
      <polygon points="612,0 825,0 825,20 602,20" fill="var(--brand-blue)"/>
    </svg>
  </section>

  <section class="card card--back">
    <div class="card__halo"></div>
    <div class="wordmark">
      <div class="wordmark__dot"></div>
      <div class="wordmark__name">
        <span class="wordmark__primary">MORAVEL</span>
        <span class="wordmark__secondary">AESTHETIC DOCTOR</span>
      </div>
    </div>

    <div class="services">
      <p>Dermal injectables <span class="sep">●</span> Plasma facials <span class="sep">●</span> Microneedling</p>
      <p>Skin boosters <span class="sep">●</span> Excessive sweating</p>
      <p>Home and Spa Based Treatments</p>
    </div>
  </section>
</body>
</html>
```